Dental Website offering Continuing Educational Courses

Need a Wordpress CMS design for a dentist website which will offer continuing education courses. The design should be professional, simple and elegant. Logo versions are provided. Please follow those colors plus one or two others that will blend well. Here's examples of other sites they like - www.pulpvantage.com, www.kqtorvi.com, www.thebrightwellinstitute.com., www.plqma.org/. Please provide designs in jpg format. If selected, then final design will be required in psd format.

Target Market(s)

dentists, endodontists (root canal specialists)

Industry/Entity Type

Education

Requirements
Must have
• Combination Horizontal / Vertical navigation. Place course titles in vertical nav in a side bar on home page. List them as Course 1, Course 2 ,etc.. total of 7 courses. The header horizontal nav should be; Home, About, Courses, Doctor Name, Faculty, FAQ, Patients, Contact.
Need placeholder to accommodate one large static image just under main nav. Need web safe fonts. Need placeholder for calendar like this example www.quietharbors.org/. Need to show a dropdown menu example. Design for 1024 x 768. Need space on home page to allow for logos of external websites/ associations. These are; www.truefieldpulp.com, www.mavolix.com, www.wfk.org/, www.kintovarhq.com/kinto/. Would like to see a row of images across the bottom of the home page like the www.plqma.org site has. Would like to show a Contact Form on the home page like the "need assistance" form example on www.thebrightwellinstitute.com. Would like to create a placeholder on the home page for an image of a doctor.
Nice to have
• 3 or 4 column footer (which features sitemap, copyright, etc..). Examples in the design for the web site’s copy styling:
o through headers
o Bulleted list
o Hyperlink
o Table

```html
<!DOCTYPE html>
<html lang="en">
<head>
<meta charset="utf-8">
<title>Tarn Teaching – Continuing Dental Education</title>
<link rel="stylesheet" href="https://fonts.googleapis.com/css2?family=Source+Sans+3:wght@400;600&display=swap">
<style>
  :root {
    --page-blue: #a9c0d6;
    --footer-blue: #c5d3e0;
    --brand-blue: #1c5a96;
    --deep-blue: #1b4f8c;
    --nav-top: #e6edf3;
    --nav-bottom: #bccddd;
    --text-dark: #2b2f33;
    --footer-text: #66717c;
    --white: #ffffff;
    --calendar-head: #c7d6e4;
    --divider: #a9c0d6;
  }
  * { box-sizing: border-box; margin: 0; padding: 0; }
  html, body { width: 956px; height: 1200px; overflow: hidden; }
  body {
    position: relative;
    background: var(--page-blue);
    font-family: "Source Sans 3", sans-serif;
    color: var(--text-dark);
  }
  a { color: inherit; text-decoration: none; }

  .site-header { position: absolute; left: 0; top: 0; width: 956px; height: 103px; background: var(--white); }
  .brand { position: absolute; left: 32px; top: 38px; display: flex; align-items: center; gap: 8px;
    font-size: 24px; font-weight: 600; color: var(--deep-blue); }
  .brand-mark { width: 22px; height: 22px; background: var(--deep-blue); }

  .social { position: absolute; left: 583px; top: 34px; display: flex; gap: 8px; list-style: none; }
  .social li { width: 18px; height: 18px; border-radius: 3px; }
  .social .s1 { background: #3b3b3b; }
  .social .s2 { background: #3aa1d8; }
  .social .s3 { background: #3b5e9c; }
  .social .s4 { background: #e8752a; }

  .search { position: absolute; left: 709px; top: 30px; width: 228px; height: 25px;
    border: 1px solid #b9c6d2; background: var(--white); }
  .search svg { position: absolute; right: 4px; top: 4px; }

  .main-nav { position: absolute; left: 267px; top: 66px; width: 670px; height: 37px;
    background: linear-gradient(var(--nav-top), var(--nav-bottom)); }
  .main-nav ul { list-style: none; }
  .main-nav > ul > li { position: absolute; top: 8px; height: 23px; line-height: 23px;
    font-size: 15px; color: var(--brand-blue); }
  .main-nav .boxed { background: var(--white); padding: 0 12px; box-shadow: 0 1px 2px rgba(0,0,0,.15); }
  .dropdown { position: absolute; left: 0; top: 26px; width: 105px; }
  .dropdown li { height: 20px; line-height: 20px; margin-bottom: 3px; padding-left: 13px;
    font-size: 12px; background: linear-gradient(#e4ebf2, #c8d6e3); box-shadow: 0 1px 2px rgba(0,0,0,.15); }

  .course-menu { position: absolute; left: 14px; top: 139px; list-style: none; }
  .course-menu li { width: 218px; height: 32px; line-height: 32px; margin-bottom: 2px; padding-left: 14px;
    font-size: 15px; color: var(--brand-blue);
    background: linear-gradient(90deg, #ffffff 0%, #ffffff 70%, #a9c0d6 100%); }

  .hero { position: absolute; left: 236px; top: 119px; width: 701px; height: 335px;
    background: radial-gradient(ellipse at 40% 55%, #e6a39a 0%, #f0d6d0 40%, #ffffff 75%); }

  .section-title { position: absolute; font-size: 18px; font-weight: 400; color: var(--brand-blue); }
  .welcome-title { left: 16px; top: 485px; }
  .welcome-text { position: absolute; left: 16px; top: 512px; width: 574px; font-size: 14.5px;
    line-height: 24px; text-align: justify; }
  .learn-more { position: absolute; left: 480px; top: 685px; width: 110px; text-align: right;
    font-size: 12px; color: var(--brand-blue); }

  .events-title { left: 640px; top: 482px; }
  .calendar { position: absolute; left: 639px; top: 507px; width: 298px; height: 194px; background: var(--white); }
  .calendar-head { height: 28px; background: var(--calendar-head); text-align: center; line-height: 28px;
    font-size: 13px; word-spacing: 8px; }
  .calendar table { width: 280px; margin: 6px 0 0 22px; border-collapse: collapse; font-size: 14px; }
  .calendar td, .calendar th { font-weight: 400; text-align: center; height: 21.3px; }

  .partners-title { left: 16px; top: 723px; }
  .carousel-arrow { position: absolute; top: 803px; width: 40px; height: 40px; border-radius: 50%; background: var(--white); }
  .carousel-arrow.prev { left: 30px; }
  .carousel-arrow.next { left: 882px; }
  .carousel-arrow svg { position: absolute; top: 10px; }
  .partner-strip { position: absolute; left: 53px; top: 762px; width: 844px; height: 122px;
    background: var(--white); display: flex; }
  .partner { display: flex; align-items: center; justify-content: center; font-size: 20px; font-weight: 600;
    color: var(--brand-blue); border-right: 1px solid var(--divider); }
  .partner:last-child { border-right: none; }

  .site-footer { position: absolute; left: 0; top: 918px; width: 956px; height: 250px; background: var(--footer-blue); }
  .footer-col { position: absolute; top: 50px; list-style: none; font-size: 14.5px; color: var(--footer-text); }
  .footer-col li { height: 34px; }
  .copyright-bar { position: absolute; left: 0; top: 1168px; width: 956px; height: 32px; background: var(--page-blue);
    text-align: center; line-height: 32px; font-size: 11px; color: var(--white); }
</style>
</head>
<body>
  <header class="site-header">
    <a class="brand" href="#"><span class="brand-mark"></span>Tarn Teaching</a>
    <ul class="social" aria-label="Social links">
      <li class="s1"></li><li class="s2"></li><li class="s3"></li><li class="s4"></li>
    </ul>
    <div class="search" role="search">
      <svg width="16" height="16" viewBox="0 0 16 16" aria-hidden="true">
        <circle cx="6" cy="6" r="4" fill="none" stroke="#1c5a96" stroke-width="2"/>
        <line x1="9" y1="9" x2="14" y2="14" stroke="#1c5a96" stroke-width="2.5"/>
      </svg>
    </div>
    <nav class="main-nav">
      <ul>
        <li class="boxed" style="left:12px">Home</li>
        <li style="left:96px">About</li>
        <li class="boxed" style="left:156px;width:82px">Courses
          <ul class="dropdown">
            <li>Courses title 1</li><li>Courses title 2</li><li>Courses title 3</li>
          </ul>
        </li>
        <li style="left:254px">Doctor Name</li>
        <li style="left:373px">Faculty</li>
        <li style="left:453px">FAQ</li>
        <li style="left:513px">Patients</li>
        <li style="left:598px">Contact</li>
      </ul>
    </nav>
  </header>

  <ul class="course-menu">
    <li>Courses title 1</li><li>Courses title 2</li><li>Courses title 3</li>
    <li>Courses title 4</li><li>Courses title 5</li><li>Courses title 6</li>
    <li>Courses title 7</li><li>Courses title 8</li><li>Courses title 9</li>
  </ul>

  <div class="hero" role="img" aria-label="Close-up of a smile with a dental mirror"></div>

  <h2 class="section-title welcome-title">Welcome to Tarn Teaching</h2>
  <p class="welcome-text">Lorem Ipsum is simply dummy text of the printing and typesetting industry. Lorem Ipsum has been the industry's standard dummy text ever since the 1500s, when an unknown printer took a galley of type and scrambled it to make a type specimen book. It has survived not only five centuries, but also the leap into electronic typesetting, remaining essentially unchanged. It was popularised in the 1960s with the release of Lettrova sheets containing Lorem Ipsum passages, and more recently with desktop publishing software like Pagewell Studio including versions of Lorem Ipsum.</p>
  <a class="learn-more" href="#">Learn more</a>

  <h2 class="section-title events-title">Events Calendar</h2>
  <div class="calendar">
    <div class="calendar-head">&lt;&lt; Jan 2012 &gt;&gt;</div>
    <table>
      <tr><th>M</th><th>T</th><th>W</th><th>T</th><th>F</th><th>S</th><th>S</th></tr>
      <tr><td>26</td><td>27</td><td>28</td><td>29</td><td>30</td><td>31</td><td>1</td></tr>
      <tr><td>2</td><td>3</td><td>4</td><td>5</td><td>6</td><td>7</td><td>8</td></tr>
      <tr><td>9</td><td>10</td><td>11</td><td>12</td><td>13</td><td>14</td><td>15</td></tr>
      <tr><td>16</td><td>17</td><td>18</td><td>19</td><td>20</td><td>21</td><td>22</td></tr>
      <tr><td>23</td><td>24</td><td>25</td><td>26</td><td>27</td><td>28</td><td>29</td></tr>
      <tr><td>30</td><td>31</td><td>1</td><td>2</td><td>3</td><td>4</td><td>5</td></tr>
    </table>
  </div>

  <h2 class="section-title partners-title">Partners and Associations</h2>
  <div class="carousel-arrow prev"><svg x="0" width="40" height="20" viewBox="0 0 40 20" aria-hidden="true"><polyline points="18,1 10,10 18,19" fill="none" stroke="#555" stroke-width="2.5"/></svg></div>
  <div class="carousel-arrow next"><svg width="40" height="20" viewBox="0 0 40 20" aria-hidden="true"><polyline points="20,1 28,10 20,19" fill="none" stroke="#555" stroke-width="2.5"/></svg></div>
  <div class="partner-strip">
    <div class="partner" style="width:212px">Kestrel Dental</div>
    <div class="partner" style="width:189px">Alignova</div>
    <div class="partner" style="width:220px">Brightly</div>
    <div class="partner" style="width:223px">Carewell Practice</div>
  </div>

  <footer class="site-footer">
    <ul class="footer-col" style="left:74px"><li>Courses title 1</li><li>Courses title 2</li><li>Courses title 3</li><li>Courses title 4</li><li>Courses title 5</li></ul>
    <ul class="footer-col" style="left:305px"><li>Courses title 1</li><li>Courses title 2</li><li>Courses title 3</li><li>Courses title 4</li><li>Courses title 5</li></ul>
    <ul class="footer-col" style="left:533px"><li>Courses title 1</li><li>Courses title 2</li><li>Courses title 3</li><li>Courses title 4</li><li>Courses title 5</li></ul>
    <ul class="footer-col" style="left:762px"><li>Courses title 1</li><li>Courses title 2</li><li>Courses title 3</li><li>Courses title 4</li><li>Courses title 5</li></ul>
  </footer>
  <div class="copyright-bar">© 2012 Tarn Teaching, All Rights Reserved</div>
</body>
</html>
```